Business cards to launch an education platform

Hi,
I am looking at having new business cards designed.
I am a startup, developing a web platform for schools and university, the education world. It's an online assessment system.
I would like a card that looks classy, and that is using the colors and the font of my logo.

I have attached:
1) my logo
2) A business card that I have designed quickly so you can have all the information required in the card, but I really don't like it.
3) The font that I am using (Lato Regular) to design my web platform
4) Some screenshots of my web platform so you can have a look at the style that I have.

Target Market(s)

Major market: Education system: Schools and university
Minor markets: Business in general

Industry/Entity Type

Business

Contact Information for Business Card

Clara Fenwick
Director

M: 0437 518 902
E: clara.fenwick@amberLoomSystems.com.au

Requirements
Must have
• The colors of my logo

```html
<!DOCTYPE html>
<html lang="en">
<head>
<meta charset="utf-8">
<title>Amber Loom Systems – Business Card</title>
<link rel="stylesheet" href="https://fonts.googleapis.com/css2?family=Lato:wght@400;700&family=Roboto+Condensed:wght@400;500&family=Arimo:wght@400;700&display=swap">
<style>
  :root {
    --stage: #8c8d8f;
    --paper: #ecedf0;
    --navy: #0d3a6e;
    --brand-blue: #1a5fa8;
    --sky: #2b9fd4;
    --cyan: #19c4e0;
    --ink-grey: #4a4f57;
    --back-dark: #0a3468;
    --back-mid: #0f5a98;
    --back-light: #1582a8;
    --back-text: #e4e8ee;
  }
  * { box-sizing: border-box; margin: 0; padding: 0; }
  html, body { width: 1105px; height: 1200px; overflow: hidden; }
  body { background: var(--stage); position: relative; }

  .card {
    position: absolute;
    left: 102px;
    width: 900px;
    height: 510px;
    overflow: hidden;
  }

  /* Front */
  .card-front { top: 60px; background: var(--paper); }
  .brand {
    position: absolute;
    top: 92px;
    left: 0; right: 0;
    display: flex;
    justify-content: center;
    align-items: center;
    gap: 26px;
  }
  .brand-mark {
    width: 112px; height: 112px;
    background: var(--brand-blue);
  }
  .brand-name {
    font-family: "Lato", sans-serif;
    font-weight: 400;
    color: var(--navy);
    font-size: 52px;
    line-height: 1.05;
    letter-spacing: 3px;
  }
  .holder {
    position: absolute;
    top: 362px; left: 0; right: 0;
    text-align: center;
    font-family: "Roboto Condensed", sans-serif;
    font-weight: 500;
    font-size: 34px;
    color: var(--navy);
  }
  .holder .role { color: var(--sky); }
  .contact {
    position: absolute;
    top: 423px; left: 0; right: 0;
    text-align: center;
    font-family: "Arimo", sans-serif;
    font-size: 23px;
    color: var(--ink-grey);
  }
  .contact .label { font-weight: 700; color: var(--navy); }
  .bands {
    position: absolute;
    left: 0; right: 0; bottom: 0;
    height: 19px;
    display: flex;
    gap: 5px;
  }
  .band { flex: 1; }
  .band-left { background: linear-gradient(90deg, #174f96, #2370bb); }
  .band-mid { background: linear-gradient(90deg, #1ea9d6, var(--cyan), #1ea9d6); }
  .band-right { background: linear-gradient(90deg, #2370bb, #174f96); }

  /* Back */
  .card-back {
    top: 630px;
    background: linear-gradient(120deg, var(--back-dark) 0%, var(--back-mid) 55%, var(--back-light) 100%);
  }
  .back-tone {
    position: absolute; inset: 0;
    background: radial-gradient(circle at 75% 70%, rgba(40,170,200,0.35), rgba(10,52,104,0) 60%);
  }
  .back-text {
    position: absolute;
    left: 284px;
    top: 185px;
    font-family: "Lato", sans-serif;
    color: var(--back-text);
  }
  .back-name {
    font-weight: 400;
    font-size: 62px;
    letter-spacing: 5px;
    line-height: 1.1;
  }
  .back-url {
    margin-top: 12px;
    font-size: 25px;
    letter-spacing: 1.5px;
  }
</style>
</head>
<body>
  <section class="card card-front">
    <div class="brand">
      <div class="brand-mark"></div>
      <div class="brand-name">AMBER LOOM<br>Systems</div>
    </div>
    <p class="holder">CLARA FENWICK - <span class="role">DIRECTOR</span></p>
    <p class="contact"><span class="label">M :</span> 0437 518 902 | <span class="label">E :</span>clara.fenwick@amberLoomSystems.com.au</p>
    <div class="bands">
      <div class="band band-left"></div>
      <div class="band band-mid"></div>
      <div class="band band-right"></div>
    </div>
  </section>

  <section class="card card-back">
    <div class="back-tone" role="img" aria-label="Soft blue background where a large brand emblem appears"></div>
    <div class="back-text">
      <p class="back-name">AMBER LOOM<br>Systems</p>
      <p class="back-url">amberLoomSystems.com.au</p>
    </div>
  </section>
</body>
</html>
```